English and Spanish Language School Needs a Business Card

Need a business card design a startup company called Maribel Language School. The company will offer English and Spanish conversational level courses designed to make the learner feel comfortable with grammar and vocabulary. We would like to see a logo with some colour that should communicate learning, growth.

Target Market(s)

Consumers and businesses

Industry/Entity Type

Education

Contact Information for Business Card

TBD

Font styles to use
Serif

Requirements
Must have
• Include the following
• Logo
• Name
• Title
• Cellphone Number
• Office Phone number
• Email address
• Office Address

```html
<!DOCTYPE html>
<html lang="en">
<head>
<meta charset="utf-8">
<title>Maribel Language School – Business Card</title>
<link rel="stylesheet" href="https://fonts.googleapis.com/css2?family=Open+Sans:wght@400;600;700&display=swap">
<style>
  :root {
    --brand-red: #c91f26;
    --brand-teal: #00a0ab;
    --card-white: #ffffff;
    --backdrop: #ecebe9;
    --text-light: #ffffff;
  }
  html, body {
    margin: 0;
    padding: 0;
    width: 1200px;
    height: 900px;
    overflow: hidden;
    background: var(--backdrop);
    font-family: "Open Sans", Arial, sans-serif;
  }
  .canvas {
    position: relative;
    width: 1200px;
    height: 900px;
  }
  .card {
    position: absolute;
    overflow: hidden;
    box-shadow: 0 6px 18px rgba(0,0,0,0.18);
  }
  .card-front {
    left: 78px;
    top: 35px;
    width: 587px;
    height: 362px;
    background: var(--card-white);
  }
  .card-back {
    left: 388px;
    top: 505px;
    width: 567px;
    height: 352px;
    background: var(--brand-red);
  }
  .card-shapes {
    position: absolute;
    inset: 0;
  }
  .wordmark {
    position: absolute;
    font-weight: 600;
    line-height: 1;
    text-align: center;
  }
  .card-front .wordmark {
    left: 0;
    width: 587px;
    top: 52px;
    color: var(--brand-red);
  }
  .wordmark-name {
    display: block;
    font-size: 76px;
    letter-spacing: -1px;
  }
  .wordmark-tagline {
    display: block;
    font-size: 22px;
    margin-top: 8px;
  }
  .card-back .wordmark {
    left: 0;
    width: 567px;
    top: 118px;
    color: var(--text-light);
  }
  .card-back .wordmark-name { font-size: 70px; }
  .card-back .wordmark-tagline { font-size: 20px; }
  .holder {
    position: absolute;
    right: 315px;
    top: 250px;
    text-align: right;
    color: var(--text-light);
  }
  .holder-name {
    font-size: 19px;
    font-weight: 700;
    margin: 0;
    line-height: 26px;
  }
  .holder-title {
    font-size: 16px;
    margin: 0;
    line-height: 22px;
  }
  .contact-list {
    position: absolute;
    left: 295px;
    top: 241px;
    margin: 0;
    padding: 0;
    list-style: none;
    color: var(--text-light);
    font-size: 16px;
    line-height: 21px;
  }
  .contact-list li {
    display: flex;
    align-items: center;
    gap: 4px;
  }
  .contact-icon {
    width: 12px;
    height: 12px;
    fill: var(--text-light);
    flex: none;
  }
  .address {
    position: absolute;
    left: 0;
    width: 587px;
    top: 315px;
    text-align: center;
    color: var(--text-light);
    font-size: 15.5px;
    margin: 0;
  }
</style>
</head>
<body>
<main class="canvas">

  <section class="card card-front" aria-label="Business card front">
    <svg class="card-shapes" width="587" height="362" viewBox="0 0 587 362" aria-hidden="true">
      <polygon points="0,188 392,188 376,214 0,214" fill="var(--brand-teal)"/>
      <polygon points="415,180 587,180 587,362 0,362 0,219 384,219" fill="var(--brand-red)"/>
    </svg>

    <div class="wordmark">
      <span class="wordmark-name">Maribel</span>
      <span class="wordmark-tagline">Language School</span>
    </div>

    <div class="holder">
      <p class="holder-name">Daniel Harper</p>
      <p class="holder-title">Managing Director</p>
    </div>

    <ul class="contact-list">
      <li>
        <svg class="contact-icon" viewBox="0 0 12 12" aria-hidden="true"><path d="M1 4c0-2 2-3 5-3s5 1 5 3l-2 1-1-2H4L3 5zM2 6h8l1 5H1z"/></svg>
        (021) 555 018 342
      </li>
      <li>
        <svg class="contact-icon" viewBox="0 0 12 12" aria-hidden="true"><path d="M3 0h6v12H3zM4 1.5v8h4v-8z"/></svg>
        (021)555019487
      </li>
      <li>
        <svg class="contact-icon" viewBox="0 0 12 12" aria-hidden="true"><path d="M0 2h12v8H0zM1 3l5 4 5-4z"/></svg>
        hello@maribelschool.com
      </li>
    </ul>

    <p class="address">48 Alder Street, Brookfield Town, 220145.</p>
  </section>

  <section class="card card-back" aria-label="Business card back">
    <div class="wordmark">
      <span class="wordmark-name">Maribel</span>
      <span class="wordmark-tagline">Language School</span>
    </div>
  </section>

</main>
</body>
</html>
```